Tolvik Commercial Cleaning is lookong for a new business card design.

A fresh new design that's professional and stylish. We need a serious upgrade to our business cards. I have included pictures of our existing ones. Our clients include professional individuals and business owners. We woupdblike something professional and upbeat. Please have fun and see what you come uo with.

Target Market(s)

Property managers, business owners, facility managers and other similar professionals

Industry/Entity Type

Janitorial

Contact Information for Business Card

Name, cell, office number, email, web address

Font styles to use
Sans Serif

Colors

Designer to choose colors to be used in the design.

Requirements
Must have
• please use the green color in our logo
Nice to have
• Bar code
Should not have
• Address

```html
<!DOCTYPE html>
<html lang="en">
<head>
<meta charset="utf-8">
<title>Tolvik Commercial Cleaning – Business Card</title>
<link rel="stylesheet" href="https://fonts.googleapis.com/css2?family=Open+Sans:wght@400;600;700&family=Quicksand:wght@700&display=swap">
<style>
  :root {
    --stage: #232323;
    --card-dark: #1f1f22;
    --brand-green: #37b653;
    --brand-green-deep: #2f9e48;
    --brand-green-light: #8fd47a;
    --accent-blue: #3d72b4;
    --text-light: #f2f2f2;
    --shade: #2f2f33;
  }
  * { box-sizing: border-box; margin: 0; padding: 0; }
  html, body {
    width: 1200px; height: 780px; overflow: hidden;
    background: var(--stage);
    font-family: "Open Sans", Arial, sans-serif;
  }
  .canvas { position: relative; width: 1200px; height: 780px; }

  .card {
    position: absolute;
    width: 540px; height: 310px;
    border-radius: 22px;
    overflow: hidden;
    box-shadow: 0 14px 30px rgba(0,0,0,.45);
  }

  /* Front */
  .card--front { left: 60px; top: 70px; }
  .front-pattern {
    position: absolute; inset: 0;
    background: linear-gradient(200deg, var(--brand-green-light) 0%, var(--brand-green) 45%, var(--brand-green-deep) 100%);
  }
  .front-brand {
    position: absolute; right: 70px; bottom: 70px;
    color: #ffffff;
    font-weight: 700; font-size: 34px; letter-spacing: .5px;
  }

  /* Back */
  .card--back {
    left: 600px; top: 400px;
    background: var(--card-dark);
    border: 3px solid var(--brand-green);
  }
  .back-block {
    position: absolute; right: 0; top: 40px;
    width: 200px; height: 140px;
    background: var(--shade);
    border-radius: 6px 0 0 6px;
  }
  .back-brand {
    position: absolute; left: 34px; top: 46px;
  }
  .back-brand__name {
    color: var(--brand-green);
    font-weight: 700; font-size: 54px; line-height: 1;
  }
  .back-brand__tagline {
    margin-top: 8px;
    color: var(--accent-blue);
    font-family: "Quicksand", "Open Sans", sans-serif;
    font-weight: 700; font-size: 17px;
  }
  .holder {
    position: absolute; right: 24px; top: 92px;
    font-weight: 700; font-size: 24px;
  }
  .holder__first { color: var(--brand-green); }
  .holder__last { color: var(--accent-blue); }

  .contact {
    position: absolute; left: 34px; bottom: 28px;
    list-style: none;
    color: var(--text-light);
    font-size: 15px; line-height: 1.55;
  }
  .contact li { display: flex; align-items: center; gap: 10px; }
  .contact svg { width: 15px; height: 15px; fill: var(--brand-green); flex: none; }
</style>
</head>
<body>
<main class="canvas">

  <section class="card card--front" aria-label="Card front">
    <div class="front-pattern" role="img" aria-label="Repeating brand-name pattern in shades of green"></div>
    <div class="front-brand">Tolvik</div>
  </section>

  <section class="card card--back" aria-label="Card back">
    <div class="back-block"></div>
    <div class="back-brand">
      <div class="back-brand__name">Tolvik</div>
      <div class="back-brand__tagline">trusted building care</div>
    </div>
    <div class="holder">
      <span class="holder__first">Dana</span>
      <span class="holder__last">Whitfield</span>
    </div>
    <ul class="contact">
      <li>
        <svg viewBox="0 0 24 24" aria-hidden="true"><path d="M6.6 10.8a15.1 15.1 0 0 0 6.6 6.6l2.2-2.2c.3-.3.7-.4 1-.2 1.1.4 2.3.6 3.6.6.6 0 1 .4 1 1V20c0 .6-.4 1-1 1A17 17 0 0 1 3 4c0-.6.4-1 1-1h3.5c.6 0 1 .4 1 1 0 1.3.2 2.5.6 3.6.1.3 0 .7-.2 1z"/></svg>
        (555) 014-2273
      </li>
      <li>
        <svg viewBox="0 0 24 24" aria-hidden="true"><path d="M2 5h20v14H2zm2 2v.5l8 5 8-5V7zm0 2.8V17h16V9.8l-8 5z"/></svg>
        dana@tolvikcleaning.com
      </li>
      <li>
        <svg viewBox="0 0 24 24" aria-hidden="true"><path d="M12 2a10 10 0 1 0 0 20 10 10 0 0 0 0-20zm6.9 6h-3a15 15 0 0 0-1.3-3.9A8 8 0 0 1 18.9 8zM12 4c.8 1.2 1.5 2.5 1.9 4h-3.8c.4-1.5 1.1-2.8 1.9-4zM4.3 14a8 8 0 0 1 0-4h3.4a16 16 0 0 0 0 4zm.8 2h3a15 15 0 0 0 1.3 3.9A8 8 0 0 1 5.1 16zm3-8h-3a8 8 0 0 1 4.3-3.9A15 15 0 0 0 8.1 8zM12 20c-.8-1.2-1.5-2.5-1.9-4h3.8c-.4 1.5-1.1 2.8-1.9 4zm2.3-6H9.7a14 14 0 0 1 0-4h4.6a14 14 0 0 1 0 4zm.3 5.9A15 15 0 0 0 15.9 16h3a8 8 0 0 1-4.3 3.9zm1.7-5.9a16 16 0 0 0 0-4h3.4a8 8 0 0 1 0 4z"/></svg>
        www.tolvikcleaning.com
      </li>
    </ul>
  </section>

</main>
</body>
</html>
```